32 x 24 Swinging Real Estate Yard Sign

We are looking to design a new sign for our business to focus on the remodeling of homes to sell. We are looking to have a yard sign that gets peoples attention and is informational. The headline will be "The Secret to Top Dollar? Remodel First.". We remodel homes for sellers with no up front cost, as they simply pay at closing. This link has more info, https://bramblecresthomes.com/Remodel
The message we want to convey to those seeing the sign is we are a one stop shop, who can renovate your home and sell it for no stress. We are licensed real estate agents and licensed contractors.
Both of these license numbers and info need to be on the design:
CADRE #02794613
Contractors License #1178524
Email: info@bramblecresthomes.com
Phone: (408)614-2907
I'll attach a sample sign we have for our agents normally as well as all brand art work.
• Pantone Colors
o #172A41
Dark blue
o #4381B1
Medium blue
o #6FA6CC
Light blue
Target Market(s)
Residential Real Estate Sellers
Industry/Entity Type
Real Estate
Colors
Designer to choose colors to be used in the design.

```html
<!DOCTYPE html>
<html lang="en">
<head>
<meta charset="utf-8">
<title>Bramblecrest Homes Remodel Yard Sign</title>
<link href="https://fonts.googleapis.com/css2?family=Montserrat:wght@300;400;500;600;700;900&display=swap" rel="stylesheet">
<style>
  :root {
    --navy: #172A41;
    --blue-mid: #4381B1;
    --blue-band: #3B6C95;
    --blue-light: #6FA6CC;
    --white: #FFFFFF;
    --backdrop: #E9ECEF;
  }
  * { margin: 0; padding: 0; box-sizing: border-box; }
  html, body {
    width: 1200px; height: 1200px; overflow: hidden;
    background: var(--backdrop);
    font-family: "Montserrat", sans-serif;
  }
  .yard-sign {
    position: absolute; left: 185px; top: 30px;
    width: 830px; height: 1140px;
    background: var(--navy);
    overflow: hidden;
  }
  .sign-shapes { position: absolute; inset: 0; }
  .brand { position: absolute; left: 0; right: 0; top: 0; text-align: center; }
  .brand-dot {
    position: absolute; left: 50%; top: 60px; width: 100px; height: 100px;
    margin-left: -50px; border-radius: 50%; background: var(--navy);
  }
  .brand-name {
    position: absolute; left: 0; right: 0; top: 200px;
    font-size: 68px; font-weight: 600; line-height: 1; letter-spacing: 1px; color: var(--navy);
  }
  .brand-sub {
    position: absolute; left: 0; right: 0; top: 290px;
    font-size: 26px; font-weight: 500; line-height: 1; letter-spacing: 16px; padding-left: 16px;
    color: var(--blue-band);
  }
  .headline-lead, .headline-main, .headline-tail, .message, .contact-email,
  .contact-phone, .contact-link, .license {
    position: absolute; left: 72px; white-space: nowrap; line-height: 1;
  }
  .headline-lead { top: 505px; font-size: 62px; font-weight: 300; color: var(--white); }
  .headline-main { top: 580px; font-size: 74px; font-weight: 900; color: var(--white); }
  .headline-tail { top: 668px; font-size: 58px; font-weight: 700; color: var(--blue-light); }
  .message { top: 752px; font-size: 23px; font-weight: 500; color: var(--white); line-height: 1.4; }
  .contact-email { top: 848px; font-size: 30px; font-weight: 500; color: var(--blue-mid); }
  .contact-phone { top: 968px; font-size: 60px; font-weight: 700; color: var(--blue-mid); }
  .contact-link { top: 1044px; font-size: 25px; font-weight: 600; color: var(--white); }
  .license { left: 592px; font-size: 18px; font-weight: 500; color: var(--blue-mid); line-height: 1.3; text-transform: uppercase; }
  .license-cadre { top: 962px; }
  .license-contractor { top: 1010px; }
</style>
</head>
<body>
  <div class="yard-sign">
    <svg class="sign-shapes" width="830" height="1140" viewBox="0 0 830 1140" aria-hidden="true">
      <polygon points="0,270 415,445 0,330" style="fill: var(--blue-band)"/>
      <polygon points="830,300 830,345 415,445" style="fill: var(--blue-band)"/>
      <polygon points="0,0 830,0 830,300 415,445 0,270" style="fill: var(--white)"/>
    </svg>

    <div class="brand">
      <div class="brand-dot"></div>
      <div class="brand-name">BRAMBLECREST</div>
      <div class="brand-sub">HOMES</div>
    </div>

    <div class="headline-lead">The Secret to</div>
    <div class="headline-main">TOP DOLLAR?</div>
    <div class="headline-tail">Remodel First.</div>
    <div class="message">One stop: we renovate your home and sell it, stress free.<br>No upfront cost – you simply pay at closing.</div>
    <div class="contact-email">info@bramblecresthomes.com</div>

    <div class="contact-phone">(408)614-2907</div>
    <div class="contact-link">bramblecresthomes.com/Remodel</div>

    <div class="license license-cadre">CADRE #02794613</div>
    <div class="license license-contractor">Contractors<br>License #1178524</div>
  </div>
</body>
</html>
```